Mental Health care Company in Washington DC

We are a new mental health care services provider in Washington DC. Please look at these sites.
https://brightwaterfamilysupport.com
https://www.quietharborinc.com
https://willowgate-dc.org/
https://www.tidepathdc.com
https://www.thelanternofdc.com

```html
<!DOCTYPE html>
<html lang="en">
<head>
<meta charset="utf-8">
<title>Sorrel Health – Mental Health Care, Washington DC</title>
<link href="https://fonts.googleapis.com/css2?family=Lexend:wght@300;400;500;600&display=swap" rel="stylesheet">
<style>
:root{
  --navy:#0c1650;
  --ink:#16203f;
  --muted:#8a93a8;
  --soft-heading:#7f8db0;
  --teal:#3cc3cf;
  --teal-dark:#2f8f95;
  --orange:#f9a65e;
  --pale:#eef6f8;
  --white:#ffffff;
  --deep-a:#0a1668;
  --deep-b:#0b2a94;
}
*{box-sizing:border-box;margin:0;padding:0}
html,body{width:1200px;height:1200px;overflow:hidden}
body{font-family:'Lexend',sans-serif;color:var(--ink);background:var(--white);position:relative}
.abs{position:absolute}
.photo{position:absolute;overflow:hidden}

/* ---------- overview column ---------- */
.overview{position:absolute;left:0;top:0;width:237px;height:1200px;background:var(--pale);overflow:hidden}
.ov-hero{left:0;top:0;width:237px;height:134px;background:linear-gradient(100deg,#0d2b3a 0%,#155a6e 45%,#3f7f8d 75%,#cfd9dc 100%)}
.ov-brand{left:11px;top:5px;font-size:6px;font-weight:500;color:var(--white);display:flex;align-items:center;gap:2px}
.ov-brand i{width:3px;height:3px;border-radius:50%;background:var(--teal);display:block}
.ov-nav{left:110px;top:7px;display:flex;gap:5px;font-size:2.6px;color:var(--white)}
.ov-cta-pill{left:192px;top:5px;width:34px;height:7px;border-radius:4px;background:var(--teal);font-size:2.4px;color:var(--navy);display:flex;align-items:center;justify-content:center}
.ov-title{left:11px;top:47px;font-size:9.5px;line-height:10px;color:var(--white);font-weight:400}
.ov-title span{color:var(--teal)}
.ov-btn{left:11px;top:82px;width:28px;height:8px;border-radius:4px;background:var(--orange);font-size:2.4px;color:var(--white);display:flex;align-items:center;justify-content:center}
.ov-popular{left:11px;top:117px;display:flex;gap:2px;align-items:center;font-size:2.8px;color:var(--white)}
.ov-popular b{font-weight:400;background:var(--teal-dark);border-radius:3px;padding:1px 3px}
.ov-rating{left:159px;top:75px;width:66px;height:47px;background:var(--white);border-radius:5px;padding:4px}
.ov-rating .dots{display:flex;gap:1px}
.ov-rating .dots i{width:7px;height:7px;border-radius:50%;background:#c9a58d;display:block}
.ov-rating p{font-size:2.4px;color:var(--muted);margin-top:3px}
.ov-rating strong{display:block;font-size:15px;font-weight:300;color:var(--navy);margin-top:2px}

.ov-kicker{font-size:2.4px;letter-spacing:.3px;color:var(--ink);font-weight:500}
.ov-h{font-size:5.4px;line-height:6.3px;color:var(--ink)}
.ov-h span{color:var(--soft-heading)}
.ov-card{width:48px;height:47px;background:var(--white);border-radius:3px;padding:5px 4px}
.ov-card svg{display:block}
.ov-card h4{font-size:3.2px;font-weight:400;margin-top:10px}
.ov-card p{font-size:2.3px;color:var(--muted);margin-top:3px;line-height:3px}
.ov-small-btn{height:8px;border-radius:4px;background:var(--orange);font-size:2.3px;color:var(--white);display:flex;align-items:center;justify-content:center}
.ov-text{font-size:2.2px;line-height:3px;color:var(--muted)}
.ov-stat{width:52px;text-align:center}
.ov-stat b{display:block;font-size:18px;font-weight:400;color:#f58a1f;line-height:20px}
.ov-stat span{font-size:2.6px;color:var(--ink)}

.ov-deep{left:0;top:503px;width:237px;height:393px;background:linear-gradient(180deg,var(--deep-a) 0%,var(--deep-b) 60%,#0a55b8 100%)}
.ov-white{color:var(--white)}
.ov-step{display:flex;gap:4px}
.ov-step i{width:8px;height:8px;border-radius:50%;background:var(--teal);flex:none;font-style:normal;font-size:2.4px;color:var(--white);display:flex;align-items:center;justify-content:center}
.ov-step h5{font-size:3px;font-weight:400;color:var(--white)}
.ov-step p{font-size:2.2px;color:#aab4dd;line-height:3px;margin-top:1px}
.ov-badge{width:22px;height:6px;border-radius:3px;background:#3e4d9c}
.ov-quote{width:50px;height:67px;border-radius:3px;background:#1c3a9e;padding:3px}
.ov-quote .stars{font-size:2.6px;color:#f7b540}
.ov-quote p{font-size:2.2px;line-height:2.9px;color:var(--white);margin-top:2px}
.ov-quote .who{position:absolute;left:3px;bottom:4px;display:flex;gap:2px;align-items:center;font-size:2.3px;color:var(--white)}
.ov-quote .who i{width:7px;height:7px;border-radius:50%;background:#d8a98b;display:block}
.ov-faq-item{width:100px;border-bottom:.5px solid #cdd6e2;font-size:2.5px;padding-bottom:3px;display:flex;justify-content:space-between}
.ov-footer{left:0;top:1106px;width:237px;height:94px;background:linear-gradient(180deg,#0b1a63,#0a2a8c)}
.ov-foot-col{font-size:2.3px;line-height:4px;color:#c9d2f0}
.ov-foot-col b{color:var(--orange);font-weight:400}
.ov-big{left:0;width:237px;text-align:center;top:1160px;font-size:32px;font-weight:400;letter-spacing:-2.5px;color:var(--white);line-height:36px}

/* ---------- detail column ---------- */
.detail{position:absolute;left:323px;top:0;width:877px;height:1200px;background:var(--pale);overflow:hidden}
.hero{left:0;top:0;width:877px;height:494px;background:linear-gradient(100deg,#071821 0%,#0f3b4c 30%,#1d6b82 55%,#3a7d8f 75%,#a9b8be 100%)}
.hero-shade{left:0;top:0;width:877px;height:494px;background:linear-gradient(90deg,rgba(4,16,24,.55) 0%,rgba(4,16,24,.1) 55%,rgba(0,0,0,0) 100%)}
.brand{left:42px;top:16px;display:flex;align-items:center;gap:6px;font-size:20px;font-weight:400;color:var(--white)}
.brand i{width:8px;height:8px;border-radius:50%;background:var(--teal);display:block}
.nav{left:410px;top:24px;display:flex;gap:17px;font-size:9.5px;color:var(--white);font-weight:400}
.nav a{color:inherit;text-decoration:none}
.nav a:first-child{color:#c5d0d6}
.nav-cta{left:710px;top:15px;width:126px;height:29px;border-radius:15px;background:#7dd8df;font-size:9px;color:var(--navy);display:flex;align-items:center;justify-content:center}
.hero-title{left:41px;top:170px;font-size:37px;line-height:36.5px;font-weight:400;color:var(--white);letter-spacing:-.3px}
.hero-title span{color:#7fd3dc}
.hero-btn{left:41px;top:300px;width:103px;height:32px;border-radius:16px;background:var(--orange);font-size:9.5px;color:var(--white);display:flex;align-items:center;justify-content:center}
.popular{left:41px;top:428px;display:flex;align-items:center;gap:7px;font-size:11px;color:var(--white)}
.popular span{font-size:8.5px;background:var(--teal-dark);border-radius:12px;padding:6px 9px}
.rating{left:588px;top:276px;width:248px;height:177px;background:var(--white);border-radius:14px;padding:17px 17px}
.rating .faces{display:flex;position:absolute;left:18px;top:18px}
.rating .faces i{width:36px;height:36px;border-radius:50%;border:2px solid var(--white);margin-right:-9px;display:block}
.rating h3{position:absolute;left:130px;top:22px;font-size:11px;font-weight:400;line-height:14px;color:var(--ink)}
.rating p{position:absolute;left:17px;top:62px;width:210px;font-size:9px;line-height:15px;color:var(--muted)}
.rating hr{position:absolute;left:17px;top:103px;width:214px;border:0;border-top:1px solid #d7e3ea}
.rating strong{position:absolute;left:15px;top:104px;font-size:57px;font-weight:300;color:var(--navy);line-height:68px}
.rating svg{position:absolute;left:101px;top:105px}
.rating em{position:absolute;right:17px;top:145px;font-style:normal;font-size:10.5px;color:var(--ink)}

.kicker{left:0;width:877px;top:580px;text-align:center;font-size:7.8px;letter-spacing:1.1px;font-weight:500;color:var(--ink)}
.sec-title{left:0;width:877px;top:603px;text-align:center;font-size:22.5px;line-height:25px;font-weight:400;color:var(--ink)}
.sec-title span{color:var(--soft-heading)}
.cards{left:62px;top:681px;display:flex;gap:18px}
.card{width:175px;height:175px;border-radius:14px;background:var(--white);padding:23px 17px;position:relative}
.card h4{position:absolute;left:17px;top:88px;font-size:13px;font-weight:400;color:var(--ink)}
.card p{position:absolute;left:17px;top:112px;width:145px;font-size:9px;line-height:15.3px;color:var(--muted);font-weight:300}
.svc-btn{left:387px;top:885px;width:103px;height:33px;border-radius:17px;background:var(--orange);font-size:9.5px;color:var(--white);display:flex;align-items:center;justify-content:center}
.photo-a{left:15px;top:1006px;width:270px;height:210px;border-radius:14px;background:linear-gradient(135deg,#0f4d62 0%,#1b7f97 50%,#2c9bb0 100%)}
.photo-b{left:307px;top:1006px;width:529px;height:210px;border-radius:14px;background:linear-gradient(100deg,#eeeae6 0%,#a8896e 40%,#6b4a36 65%,#3d3531 100%)}
</style>
</head>
<body>

<!-- ===== Full-page overview ===== -->
<section class="overview" aria-label="Full page overview">
  <div class="photo ov-hero abs" role="img" aria-label="Two clinicians in teal scrubs reviewing a tablet"></div>
  <div class="ov-brand abs"><i></i>Sorrel Health</div>
  <nav class="ov-nav abs"><span>Home</span><span>About</span><span>Services</span><span>Our Doctors</span><span>FAQ</span><span>Contact</span></nav>
  <div class="ov-cta-pill abs">Make an Appointment</div>
  <h1 class="ov-title abs">Leading Mental<br>Care for a <span>Healthier</span><br>You and Always</h1>
  <div class="ov-btn abs">Our Services</div>
  <div class="ov-popular abs">Popular services <b>Individual Therapy</b><b>Medication Management</b><b>Psychiatry</b></div>
  <div class="ov-rating abs">
    <div class="dots"><i></i><i></i><i></i></div>
    <p>Your health is your greatest asset. Modern medicine empowers you with care</p>
    <strong>4.9</strong>
  </div>

  <div class="ov-kicker abs" style="left:0;width:237px;top:158px;text-align:center">COMPREHENSIVE CARE SERVICES</div>
  <div class="ov-h abs" style="left:0;width:237px;top:164px;text-align:center">Personalized Healthcare <span>Innovative Mental<br>Care Solutions</span></div>
  <div class="ov-card abs" style="left:16px;top:185px"><svg width="8" height="8"><rect x="1" y="1" width="6" height="6" rx="1" fill="none" stroke="#3cc3cf" stroke-width=".8"/></svg><h4>Medical Services</h4><p>We offer an array of medical support services to treat your health.</p></div>
  <div class="ov-card abs" style="left:69px;top:185px"><svg width="8" height="8"><circle cx="4" cy="4" r="3.5" fill="#3cc3cf"/></svg><h4>Behavioral Health</h4><p>Mental health is essential to overall health, experts are ready.</p></div>
  <div class="ov-card abs" style="left:121px;top:185px"><svg width="9" height="8"><circle cx="2" cy="3" r="1.5" fill="#3cc3cf"/><circle cx="4.5" cy="2.5" r="1.8" fill="#3cc3cf"/><circle cx="7" cy="3" r="1.5" fill="#3cc3cf"/></svg><h4>Human Services</h4><p>We connect people with holistic services for wellbeing.</p></div>
  <div class="ov-card abs" style="left:172px;top:185px"><svg width="8" height="8"><path d="M4 7 1 4a1.8 1.8 0 0 1 3-2.3A1.8 1.8 0 0 1 7 4Z" fill="#3cc3cf"/></svg><h4>Spiritual Needs</h4><p>Faith comes in many forms. Learn how we can help.</p></div>
  <div class="ov-small-btn abs" style="left:104px;top:240px;width:28px">Our Services</div>

  <div class="photo abs" style="left:7px;top:272px;width:68px;height:54px;border-radius:3px;background:linear-gradient(135deg,#0f4d62,#2c9bb0)" role="img" aria-label="Nurse in scrubs holding a tablet"></div>
  <div class="photo abs" style="left:83px;top:272px;width:142px;height:86px;border-radius:3px;background:linear-gradient(100deg,#e8e3dc,#9b7c62 50%,#4a3a31)" role="img" aria-label="Doctor greeting a patient in a bright clinic"></div>
  <div class="ov-kicker abs" style="left:11px;top:367px">EMPOWERING HEALTHCARE</div>
  <div class="ov-h abs" style="left:11px;top:373px;font-size:8px;line-height:9px">About Us</div>
  <p class="ov-text abs" style="left:83px;top:375px;width:72px">Sorrel Health is a mental health provider offering caring services and modern solutions for every patient in our city, with a steady commitment to quality.</p>
  <p class="ov-text abs" style="left:157px;top:375px;width:68px">Founded in Washington, we began as a small clinic with a vision to change care. We have grown our services and our team over time.</p>
  <div class="ov-stat abs" style="left:14px;top:417px"><b>13</b><span>Care Options</span></div>
  <div class="ov-stat abs" style="left:66px;top:417px"><b>93</b><span>Happy Patients</span></div>
  <div class="ov-stat abs" style="left:118px;top:417px"><b>9</b><span>Years of Service</span></div>
  <div class="ov-stat abs" style="left:170px;top:417px"><b>68</b><span>Cases Handled</span></div>

  <div class="ov-deep abs"></div>
  <div class="photo abs" style="left:11px;top:465px;width:214px;height:95px;border-radius:3px;background:linear-gradient(100deg,#f2f4f6,#b8cfd8 50%,#d9b98c)" role="img" aria-label="Therapist taking notes during a session with a client"></div>
  <div class="ov-kicker abs ov-white" style="left:17px;top:594px;font-size:2.2px">COMPREHENSIVE MEDICAL SERVICES</div>
  <div class="ov-h abs ov-white" style="left:17px;top:600px;font-size:8.5px;line-height:10px">Exceptional Care,<br><span style="color:#7fd3dc">Patient-Focused</span></div>
  <div class="ov-step abs" style="left:17px;top:628px;width:90px"><i>1</i><div><h5>Research &amp; Development</h5><p>We shape care plans with customized strategies.</p></div></div>
  <div class="ov-step abs" style="left:17px;top:651px;width:90px"><i>2</i><div><h5>Healthcare Excellence</h5><p>We improve lives through advanced, caring services.</p></div></div>
  <div class="ov-step abs" style="left:17px;top:674px;width:90px"><i>3</i><div><h5>Patient-Centered Care</h5><p>We enhance lives through thoughtful care.</p></div></div>
  <div class="photo abs" style="left:121px;top:584px;width:99px;height:116px;border-radius:3px;background:linear-gradient(160deg,#dbe6ea,#6f9db0 55%,#2f5f7a)" role="img" aria-label="Nurse comforting an elderly man in a wheelchair"></div>
  <div class="ov-badge abs" style="left:19px;top:727px"></div>
  <div class="ov-badge abs" style="left:58px;top:727px"></div>
  <div class="ov-badge abs" style="left:90px;top:727px"></div>
  <div class="ov-badge abs" style="left:124px;top:727px"></div>
  <div class="ov-badge abs" style="left:157px;top:727px"></div>
  <div class="ov-badge abs" style="left:195px;top:727px"></div>
  <div class="ov-kicker abs ov-white" style="left:0;width:237px;top:760px;text-align:center;font-size:2.2px">PATIENT TESTIMONIALS</div>
  <div class="ov-h abs ov-white" style="left:0;width:237px;top:766px;text-align:center;font-size:8.5px;line-height:10px">What Our Patients<br>Say <span style="color:#7fd3dc">About Us</span></div>
  <div class="ov-quote abs" style="left:11px;top:793px"><div class="stars">★★★★★</div><p>At Sorrel Health I am more than a patient. Their care made a real difference to my health.</p><div class="who"><i></i>Nora Ellison</div></div>
  <div class="ov-quote abs" style="left:66px;top:793px"><div class="stars">★★★★★</div><p>Exceptional service with a human touch. Everyone is kind and I always leave informed.</p><div class="who"><i></i>Caleb Whitfield</div></div>
  <div class="ov-quote abs" style="left:121px;top:793px"><div class="stars">★★★★★</div><p>The best choice for my family. Friendly, efficient staff make care simple and easy.</p><div class="who"><i></i>Priya Haldane</div></div>
  <div class="ov-quote abs" style="left:176px;top:793px"><div class="stars">★★★★★</div><p>A modern clinic and caring team. Every visit is smooth and stress free for me.</p><div class="who"><i></i>Maya Corwin</div></div>

  <div class="ov-kicker abs" style="left:17px;top:919px;font-size:2.2px">FREQUENTLY ASKED QUESTIONS</div>
  <div class="ov-h abs" style="left:17px;top:926px;font-size:8.5px;line-height:10px">Your Guide to<br><span>Common Questions</span></div>
  <p class="ov-text abs" style="left:17px;top:950px;width:90px">We are here to help with any questions about our services and appointments.</p>
  <div class="ov-faq-item abs" style="left:120px;top:927px"><span>How can I begin my journey?</span><span>+</span></div>
  <div class="ov-faq-item abs" style="left:120px;top:941px;border:0"><span>Do you offer virtual consultations?</span><span>–</span></div>
  <p class="ov-text abs" style="left:120px;top:947px;width:100px;border-bottom:.5px solid #cdd6e2;padding-bottom:3px">Yes, we offer secure video sessions for therapy and follow-ups.</p>
  <div class="ov-faq-item abs" style="left:120px;top:965px"><span>What areas do you specialize in?</span><span>+</span></div>
  <div class="ov-faq-item abs" style="left:120px;top:979px"><span>Do you provide urgent care?</span><span>+</span></div>

  <div class="photo abs" style="left:11px;top:1012px;width:214px;height:94px;border-radius:3px;background:linear-gradient(100deg,#4b6a78,#1f6e84 55%,#0f4050)" role="img" aria-label="Clinicians in scrubs smiling in a hallway"></div>
  <div class="abs" style="left:11px;top:1046px;width:214px;text-align:center;font-size:5.2px;line-height:6px;color:var(--white)">Start Your Journey to Better Mental<br>Health Today</div>
  <div class="ov-small-btn abs" style="left:106px;top:1062px;width:24px;height:6px">Join Us Now</div>

  <div class="ov-footer abs"></div>
  <div class="ov-brand abs" style="top:1121px;font-size:7px"><i></i>Sorrel Health</div>
  <p class="ov-text abs" style="left:11px;top:1140px;width:62px;color:#aab4dd">We are committed to enhancing patient care through compassion and skill.</p>
  <div class="ov-foot-col abs" style="left:99px;top:1120px"><b>Office</b><br>USA – 48 Linden Row,<br>Washington, DC 20010<br>hello@sorrelhealth.org<br><b>+1-202-555-0147</b></div>
  <div class="ov-foot-col abs" style="left:143px;top:1120px"><b>Links</b><br>Home<br>About<br>Services<br>Our Doctors<br>Contacts</div>
  <div class="ov-foot-col abs" style="left:187px;top:1120px"><b>Follow Us</b><br>Community<br>Newsletter<br>Events<br>Journal</div>
  <div class="ov-big abs">Mental Health</div>
</section>

<!-- ===== Detail view ===== -->
<section class="detail" aria-label="Homepage detail">
  <div class="photo hero abs" role="img" aria-label="Two clinicians in teal scrubs and a white coat reviewing a tablet together"></div>
  <div class="hero-shade abs"></div>

  <div class="brand abs"><i></i>Sorrel Health</div>
  <nav class="nav abs"><a>Home</a><a>About</a><a>Services</a><a>Our Doctors</a><a>FAQ</a><a>Contact</a></nav>
  <div class="nav-cta abs">Make an Appointment</div>

  <h1 class="hero-title abs">Leading Mental<br>Care for a <span>Healthier</span><br>You and Always</h1>
  <div class="hero-btn abs">Our Services</div>
  <div class="popular abs">Popular services <span>Individual Therapy</span><span>Medication Management</span><span>Psychiatry</span></div>

  <div class="rating abs">
    <div class="faces">
      <i role="img" aria-label="Patient portrait" style="background:#c7a58c"></i>
      <i role="img" aria-label="Patient portrait" style="background:#8d6a52"></i>
      <i role="img" aria-label="Patient portrait" style="background:#b98b6c"></i>
    </div>
    <h3>Happy patients,<br>exceptional care!</h3>
    <p>Your health is your greatest asset. Modern medicine empowers you with care</p>
    <hr>
    <strong>4.9</strong>
    <svg width="22" height="21" viewBox="0 0 24 24"><path d="M12 2l2.9 6.6 7.1.6-5.4 4.7 1.6 7L12 17.3 5.8 20.9l1.6-7L2 9.2l7.1-.6Z" fill="#f7c23c"/></svg>
    <em>{Rating}</em>
  </div>

  <div class="kicker abs">COMPREHENSIVE CARE SERVICES</div>
  <h2 class="sec-title abs">Personalized Healthcare <span>Innovative Mental<br>Care Solutions</span></h2>

  <div class="cards abs">
    <article class="card">
      <svg width="32" height="32" viewBox="0 0 32 32" fill="none" stroke="#3cc3cf" stroke-width="1.4"><rect x="2" y="2" width="22" height="28" rx="2"/><circle cx="16" cy="10" r="4"/><path d="M10 19h8M6 23h8M6 26h6"/><rect x="20" y="18" width="10" height="10" rx="2"/><path d="M25 20v6M22 23h6"/></svg>
      <h4>Medical Services</h4>
      <p>We offer an array of medical support services meant to treat and manage your health.</p>
    </article>
    <article class="card">
      <svg width="32" height="32" viewBox="0 0 32 32"><path d="M16 2C9 2 4 7 4 13.5c0 3.6 1.6 6 3.4 7.8V30h11v-4h4a3 3 0 0 0 3-3v-4l3-1-3-5C25.4 6.5 21 2 16 2Z" fill="#3cc3cf"/><circle cx="15" cy="13" r="3.2" fill="#fff"/><path d="M15 6.5v3M15 16.5v3M8.5 13h3M18.5 13h3M10.5 8.5l2 2M17.5 15.5l2 2M19.5 8.5l-2 2M12.5 15.5l-2 2" stroke="#fff" stroke-width="1.6"/></svg>
      <h4>Behavioral Health</h4>
      <p>Mental health is essential to overall health, and we have experts ready to help.</p>
    </article>
    <article class="card">
      <svg width="32" height="32" viewBox="0 0 32 32" fill="#3cc3cf"><circle cx="16" cy="9" r="4.5"/><circle cx="7" cy="11" r="3.3"/><circle cx="25" cy="11" r="3.3"/><path d="M8 24c0-5 3.6-8 8-8s8 3 8 8Z"/><path d="M1 23c0-4 2.7-6 6-6 1 0 2 .2 2.7.6C7.9 19 7 21 7 23Z"/><path d="M31 23c0-4-2.7-6-6-6-1 0-2 .2-2.7.6C24.1 19 25 21 25 23Z"/></svg>
      <h4>Human Services</h4>
      <p>We connect people with holistic services that drive comprehensive wellbeing.</p>
    </article>
    <article class="card">
      <svg width="32" height="32" viewBox="0 0 32 32"><path d="M16 29 4 17A7 7 0 0 1 16 7a7 7 0 0 1 12 10Z" fill="#3cc3cf"/><path d="M4 17h7l2-4 3 8 2-4h10" fill="none" stroke="#fff" stroke-width="1.8"/></svg>
      <h4>Spiritual Needs</h4>
      <p>Faith comes in many forms, so do individual spiritual needs. Learn how we can help.</p>
    </article>
  </div>

  <div class="svc-btn abs">Our Services</div>

  <div class="photo photo-a" role="img" aria-label="Smiling nurse in teal scrubs holding a tablet"></div>
  <div class="photo photo-b" role="img" aria-label="Doctor in a white coat greeting a patient in a warm clinic"></div>
</section>

</body>
</html>
```